A revolutionary website for a revolutionary construction company

I am looking for inspirations... please help me and read the attached brief

I would like to achieve a website design that is modern, premium dynamic and drives emotions. I do not want a design that can be found on a normal template. Having that said, I would also like the utilisation of Illustrations that are relation to the company’s services…. Also would like to have illustrations dynamic when you navigate on them. So a young, dynamic and parallax design website that will show off these requirements. Also to add trust, with all pages designed.

please see attachements.
Updates

Low design quality

Target Market(s)

Please read brief

Number of Pages Required

5+ page

Font styles to use
Other font styles liked:
• Futura

Requirements
Must have
• Please read brief - colours to be matching logo colours
Nice to have
Should not have

```html
<!DOCTYPE html>
<html lang="en">
<head>
<meta charset="utf-8">
<title>Ironline Builds</title>
<link href="https://fonts.googleapis.com/css2?family=Jost:wght@400;500;600&family=Oswald:wght@300;400;600;700&display=swap" rel="stylesheet">
<style>
:root{
  --maroon:#7d1a3d;
  --slate:#4e4849;
  --ink:#3b3335;
  --white:#ffffff;
  --muted:#5a5556;
}
*{margin:0;padding:0;box-sizing:border-box}
html,body{width:1200px;height:3404px;overflow:hidden;background:var(--white)}
body{position:relative;font-family:"Jost",sans-serif;color:var(--ink)}
.abs{position:absolute}
.center{left:0;width:1200px;text-align:center}

/* header */
.site-header{position:absolute;top:0;left:0;width:1200px;height:130px;background:var(--white);z-index:5}
.brand-tab{position:absolute;left:98px;top:0;width:218px;height:208px;z-index:6}
.brand-mark{position:absolute;left:76px;top:58px;width:66px;height:66px;border:2px solid var(--slate);border-radius:50%}
.brand-name{position:absolute;left:0;top:133px;width:218px;text-align:center;font-weight:600;font-size:12px;letter-spacing:3px;color:var(--maroon)}
.brand-tag{position:absolute;left:0;top:151px;width:218px;text-align:center;font-size:9px;color:var(--maroon)}
.main-nav{position:absolute;top:58px;left:472px;font-size:15px;color:var(--muted)}
.main-nav span{position:absolute;white-space:nowrap}
.main-nav .is-active{color:var(--maroon);font-weight:500}
.social{position:absolute;top:61px;width:13px;height:13px;border-radius:50%;background:var(--muted)}

/* hero */
.hero{position:absolute;top:130px;left:0;width:1200px;height:760px;
  background:
    radial-gradient(ellipse 260px 200px at 250px 330px,rgba(255,236,140,.75),rgba(255,236,140,0) 70%),
    radial-gradient(ellipse 700px 160px at 900px 440px,rgba(70,48,22,.55),rgba(70,48,22,0) 75%),
    radial-gradient(ellipse 260px 360px at 200px 560px,rgba(60,45,22,.6),rgba(60,45,22,0) 75%),
    linear-gradient(180deg,#f4cd42 0%,#edbd35 22%,#d9a52f 40%,#a67e2b 55%,#6b5024 66%,#45361f 76%,#2f2719 100%)}
.hero-title{top:548px;font-family:"Oswald",sans-serif;font-weight:600;font-size:46px;letter-spacing:12px;color:var(--white)}
.hero-sub{top:604px;font-family:"Oswald",sans-serif;font-weight:300;font-size:23px;color:var(--white)}
.hero-chevron{left:592px;top:712px}

/* intro */
.intro-title{top:874px;font-family:"Oswald",sans-serif;font-weight:600;font-size:48px;letter-spacing:12px;color:var(--maroon)}
.intro-sub{top:934px;font-family:"Oswald",sans-serif;font-weight:300;font-size:23px;color:var(--ink)}
.rule{position:absolute;height:3px;width:52px;left:574px}
.rule--maroon{background:var(--maroon)}
.rule--white{background:var(--white)}
.intro-copy{top:988px;left:205px;width:790px;text-align:center;font-size:13px;line-height:21px;color:var(--muted)}
.btn{position:absolute;background:var(--maroon);color:var(--white);font-weight:600;text-align:center;border-radius:30px}
.btn--lg{left:514px;top:1105px;width:172px;height:52px;line-height:52px;font-size:18px}

/* services */
.services{position:absolute;top:1240px;left:0;width:1200px;height:704px;
  background:
    radial-gradient(ellipse 500px 300px at 300px 250px,rgba(120,114,115,.45),rgba(120,114,115,0) 70%),
    radial-gradient(ellipse 420px 360px at 980px 520px,rgba(140,134,135,.4),rgba(140,134,135,0) 70%),
    linear-gradient(160deg,#5a5455 0%,#4b4546 50%,#625c5d 100%)}
.section-title{font-family:"Oswald",sans-serif;font-weight:600;font-size:46px;letter-spacing:12px}
.services-title{top:1374px;color:var(--white)}
.service-img{position:absolute;width:311px;height:205px}
.service-label{position:absolute;font-family:"Oswald",sans-serif;font-weight:600;font-size:26px;color:var(--white)}
.service-btn{left:203px;top:1583px;width:120px;height:34px;line-height:34px;font-size:13px}
.pager{position:absolute;top:1878px;height:3px;background:var(--white)}

/* news */
.news-bg{position:absolute;left:0;top:1944px;width:1200px;height:660px;
  background:
    radial-gradient(ellipse 400px 260px at 150px 120px,rgba(225,222,224,.6),rgba(225,222,224,0) 70%),
    radial-gradient(ellipse 400px 260px at 1050px 200px,rgba(225,222,224,.6),rgba(225,222,224,0) 70%),
    linear-gradient(180deg,#ffffff,#f3f2f3)}
.news-title{top:2016px;color:var(--maroon)}
.news-img{position:absolute;top:2131px;width:315px;height:219px}
.news-head{position:absolute;top:2364px;font-family:"Oswald",sans-serif;font-weight:400;font-size:27px;color:var(--maroon);white-space:nowrap}
.news-copy{position:absolute;top:2413px;width:295px;font-size:13px;line-height:19px;color:var(--ink)}
.news-btn{top:2484px;width:120px;height:37px;line-height:37px;font-size:13px}

/* contact */
.contact{position:absolute;top:2600px;left:0;width:1200px;height:600px;background:var(--slate)}
.contact-title{top:2682px;color:var(--white)}
.field{position:absolute;background:var(--white);font-size:10px;font-weight:600;color:var(--maroon);padding:24px 0 0 30px;letter-spacing:.3px}
.submit{left:540px;top:3108px;width:120px;height:35px;line-height:35px;font-size:13px}

/* footer */
.footer-mark{left:577px;top:3232px;width:46px;height:46px;border:2px solid var(--slate);border-radius:50%}
.footer-name{top:3284px;font-weight:600;font-size:9px;letter-spacing:3px;color:var(--maroon)}
.footer-tag{top:3297px;font-size:6px;color:var(--maroon)}
.footer-social{position:absolute;top:3333px;width:11px;height:11px;border-radius:50%;background:var(--ink)}
.copyright{top:3357px;font-size:13px;color:var(--ink)}
</style>
</head>
<body>

<header class="site-header">
  <nav class="main-nav" aria-label="Main">
    <span class="is-active" style="left:0">Home</span>
    <span style="left:76px">About Us</span>
    <span style="left:176px">Services</span>
    <span style="left:269px">Latest News</span>
    <span style="left:392px">Contact Us</span>
  </nav>
  <span class="social" style="left:998px"></span>
  <span class="social" style="left:1035px"></span>
  <span class="social" style="left:1073px"></span>
</header>

<div class="brand-tab">
  <svg width="218" height="208" class="abs" style="left:0;top:0">
    <path d="M0 0 H218 V208 Q109 182 0 208 Z" fill="#ffffff"/>
  </svg>
  <span class="brand-mark"></span>
  <div class="brand-name">Ironline Builds</div>
  <div class="brand-tag">Building with peace of mind</div>
</div>

<section class="hero" role="img" aria-label="Silhouettes of surveyors, tower cranes and a rising building against a golden sunset sky"></section>
<div class="abs center hero-title">Ironline Builds</div>
<div class="abs center hero-sub">Building with peace of mind</div>
<svg class="abs hero-chevron" width="16" height="10"><path d="M1 1 L8 8 L15 1" stroke="#fff" stroke-width="2" fill="none"/></svg>

<svg class="abs" style="left:0;top:760px" width="1200" height="140">
  <path d="M0 92 Q600 -10 1200 126 V140 H0 Z" fill="#7d1a3d"/>
  <path d="M0 100 Q600 10 1200 90 V140 H0 Z" fill="#ffffff"/>
</svg>

<h1 class="abs center intro-title">Ironline Builds</h1>
<div class="abs center intro-sub">Building with peace of mind</div>
<span class="rule rule--maroon" style="top:977px"></span>
<p class="abs intro-copy">Sed ut perspiciatis unde omnis iste natus error sit voluptatem accusantium doloremque laudantium, totam rem aperiam, eaque ipsa quae ab illo inventore veritatis et quasi architecto beatae vitae dicta sunt explicabo. Nemo enim ipsam voluptatem quia voluptas sit aspernatur aut odit aut fugit, sed quia consequuntur magni dolores eos qui ratione voluptatem sequi nesciunt. Neque porro quisquam est, qui dolorem ipsum quia dolor sit amet.</p>
<span class="btn btn--lg">READ MORE</span>

<section class="services" role="img" aria-label="Faded steel roof trusses seen from below"></section>
<svg class="abs" style="left:0;top:1170px" width="1200" height="140">
  <path d="M0 0 H1200 V6 Q600 150 0 40 Z" fill="#ffffff"/>
  <path d="M0 40 Q600 150 1200 6 V44 Q600 190 0 66 Z" fill="#7d1a3d"/>
</svg>
<h2 class="abs center section-title services-title">Services</h2>
<span class="rule rule--white" style="top:1444px"></span>

<div class="service-img" style="left:111px;top:1501px;background:
  radial-gradient(ellipse 120px 90px at 120px 150px,rgba(255,214,120,.95),rgba(255,214,120,0) 75%),
  radial-gradient(ellipse 140px 80px at 240px 190px,rgba(40,30,28,.85),rgba(40,30,28,0) 75%),
  linear-gradient(160deg,#3d4d70 0%,#8e7a7e 30%,#e4a45a 55%,#f0c27c 70%,#e8dbe6 100%)" role="img" aria-label="Crane and workers silhouetted at sunset"></div>
<span class="btn service-btn">READ MORE</span>
<div class="service-label" style="left:122px;top:1724px">Fit-out</div>

<div class="service-img" style="left:448px;top:1536px;background:
  radial-gradient(ellipse 60px 40px at 165px 70px,rgba(230,200,150,.7),rgba(230,200,150,0) 75%),
  linear-gradient(180deg,rgba(0,0,0,0) 70%,rgba(60,50,42,.35) 100%),
  linear-gradient(90deg,#fafafa 0%,#e6e4e1 35%,#9a8a7a 58%,#5a4a3c 78%,#3a3029 100%)" role="img" aria-label="Kitchen interior shifting from pencil sketch to finished render"></div>
<div class="service-label" style="left:455px;top:1758px">Design and construct</div>

<div class="service-img" style="left:784px;top:1500px;background:
  radial-gradient(ellipse 90px 70px at 160px 110px,rgba(60,100,200,.8),rgba(60,100,200,0) 75%),
  radial-gradient(ellipse 60px 60px at 220px 160px,rgba(40,40,110,.6),rgba(40,40,110,0) 75%),
  linear-gradient(180deg,#f3f7fc 0%,#cddcf0 40%,#7f9fdc 70%,#4367c2 100%)" role="img" aria-label="Flat blue illustration of cranes and a worker with a building site"></div>
<div class="service-label" style="left:796px;top:1721px">Construction</div>

<span class="pager" style="left:561px;width:42px"></span>
<span class="pager" style="left:614px;width:8px"></span>
<span class="pager" style="left:629px;width:8px"></span>

<section aria-label="Latest news">
  <div class="news-bg" role="img" aria-label="Faint wireframe geometric background"></div>
  <h2 class="abs center section-title news-title">Latest News</h2>
  <span class="rule rule--maroon" style="top:2086px"></span>

  <div class="news-img" style="left:110px;background:
    radial-gradient(ellipse 80px 60px at 120px 70px,rgba(40,70,160,.8),rgba(40,70,160,0) 75%),
    radial-gradient(ellipse 90px 70px at 260px 150px,rgba(200,205,200,.8),rgba(200,205,200,0) 75%),
    linear-gradient(135deg,#2e3b5e 0%,#5d6a82 40%,#a7adb3 70%,#d3d6d4 100%)" role="img" aria-label="Team reviewing plans and a hard hat on a desk"></div>
  <div class="news-head" style="left:114px">Finibus Bonorum et Malorum</div>
  <p class="news-copy" style="left:114px">Sed ut perspiciatis unde omnis iste natus error sit voluptatem accusantium doloremque laudantium, totam rem aperiam.</p>
  <span class="btn news-btn" style="left:112px">READ MORE</span>

  <div class="news-img" style="left:444px;background:
    radial-gradient(ellipse 90px 60px at 170px 90px,rgba(245,245,240,.9),rgba(245,245,240,0) 75%),
    radial-gradient(ellipse 130px 50px at 110px 175px,rgba(90,120,60,.85),rgba(90,120,60,0) 75%),
    linear-gradient(180deg,#e2ecf2 0%,#c8d3d0 40%,#7d9a55 70%,#e6e6e2 100%)" role="img" aria-label="Modern house render emerging from an architectural drawing"></div>
  <div class="news-head" style="left:449px">Finibus Bonorum et Malorum</div>
  <p class="news-copy" style="left:449px">Sed ut perspiciatis unde omnis iste natus error sit voluptatem accusantium doloremque laudantium, totam rem aperiam.</p>
  <span class="btn news-btn" style="left:445px">READ MORE</span>

  <div class="news-img" style="left:778px;background:
    radial-gradient(ellipse 90px 50px at 150px 50px,rgba(230,150,50,.75),rgba(230,150,50,0) 75%),
    radial-gradient(ellipse 120px 60px at 150px 140px,rgba(240,238,232,.95),rgba(240,238,232,0) 75%),
    linear-gradient(160deg,#7f858b 0%,#b8b7b2 40%,#dedbd4 65%,#8f9296 100%)" role="img" aria-label="Two builders in hard hats studying blueprints on a table"></div>
  <div class="news-head" style="left:784px">Finibus Bonorum et Malorum</div>
  <p class="news-copy" style="left:784px">Sed ut perspiciatis unde omnis iste natus error sit voluptatem accusantium doloremque laudantium, totam rem aperiam.</p>
  <span class="btn news-btn" style="left:784px">READ MORE</span>
</section>

<section class="contact" aria-label="Contact"></section>
<svg class="abs" style="left:0;top:2550px" width="1200" height="90">
  <path d="M0 0 H1200 V6 Q600 70 0 0 Z" fill="#f3f2f3"/>
  <path d="M0 6 Q600 70 1200 6 V32 Q600 90 0 28 Z" fill="#7d1a3d"/>
</svg>
<h2 class="abs center section-title contact-title">Contact Us</h2>
<span class="rule rule--white" style="top:2752px"></span>

<div class="field" style="left:197px;top:2811px;width:394px;height:52px">FIRST NAME</div>
<div class="field" style="left:608px;top:2810px;width:395px;height:52px">LAST NAME</div>
<div class="field" style="left:197px;top:2889px;width:394px;height:52px">EMAIL</div>
<div class="field" style="left:608px;top:2888px;width:395px;height:52px">PHONE</div>
<div class="field" style="left:197px;top:2967px;width:809px;height:111px">MESSAGE</div>
<span class="btn submit">SUBMIT</span>

<footer>
  <span class="abs footer-mark"></span>
  <div class="abs center footer-name">Ironline Builds</div>
  <div class="abs center footer-tag">Building with peace of mind</div>
  <span class="footer-social" style="left:537px"></span>
  <span class="footer-social" style="left:573px"></span>
  <span class="footer-social" style="left:611px"></span>
  <span class="footer-social" style="left:648px"></span>
  <div class="abs center copyright">© 2020 | www.ironlinebuilds.com</div>
</footer>

</body>
</html>
```